A Small Coastal town of New Zealand book!

we want a cool book cover for our book titled; Wharepuke Bay & Its Hidden Western Coves - Old Stories, Diving, Tramping and places to see...

attached are some screenshots of books we found that were similar to the topic i cover.

also attached are some screenshots of some ideas i have been playing with my self with myself on canva...

i quite like the first one how he managed to put 5 images there without making it look too busy...

Tourists

Tourism

Serif
Sans Serif

• Nice coastal image and good fonts and text placement
• not to busy...

```html
<!DOCTYPE html>
<html lang="en">
<head>
<meta charset="UTF-8">
<title>Wharepuke Bay &amp; Its Hidden Western Coves – Book Cover</title>
<link rel="stylesheet" href="https://fonts.googleapis.com/css2?family=Tinos:ital,wght@0,400;0,700;1,400;1,700&display=swap">
<style>
  :root {
    --page-bg: #d3d8da;
    --navy-band: #1f4660;
    --deep-band: #1b2e3c;
    --sticker-blue: #4a7fe8;
    --text-light: #ffffff;
    --sky-top: #8fa9bd;
    --sky-bottom: #5f87a6;
    --hill-green: #5f9a34;
    --water-blue: #a9bccb;
  }
  * { box-sizing: border-box; margin: 0; padding: 0; }
  html, body {
    width: 1200px;
    height: 989px;
    overflow: hidden;
    background: var(--page-bg);
  }
  .canvas {
    position: relative;
    width: 1200px;
    height: 989px;
  }
  .cover {
    position: absolute;
    left: 290px;
    top: 45px;
    width: 620px;
    height: 900px;
    overflow: hidden;
    font-family: "Tinos", "Times New Roman", serif;
    color: var(--text-light);
    box-shadow: 0 10px 30px rgba(0,0,0,0.25);
  }
  .sky-photo {
    position: absolute;
    left: 0; top: 0;
    width: 100%; height: 160px;
    background: linear-gradient(180deg, var(--sky-top) 0%, #b7c6cf 45%, var(--sky-bottom) 100%);
  }
  .title-band {
    position: absolute;
    left: 0; top: 155px;
    width: 100%; height: 218px;
    background: var(--navy-band);
  }
  .title-main {
    position: absolute;
    right: 42px;
    top: 42px;
    font-size: 56px;
    font-weight: 400;
    letter-spacing: 0.5px;
    line-height: 1;
    white-space: nowrap;
  }
  .title-sub {
    position: absolute;
    right: 42px;
    top: 118px;
    font-style: italic;
    font-size: 26px;
    line-height: 1.05;
    text-align: left;
    white-space: nowrap;
  }
  .title-sub .amp {
    font-size: 44px;
    vertical-align: -4px;
    margin-right: 6px;
  }
  .tagline-band {
    position: absolute;
    left: 0; top: 373px;
    width: 100%; height: 90px;
    background: var(--deep-band);
    display: flex;
    align-items: center;
    justify-content: center;
  }
  .tagline {
    font-size: 22px;
    letter-spacing: 0.1px;
  }
  .landscape-photo {
    position: absolute;
    left: 0; top: 463px;
    width: 100%; height: 437px;
    background: linear-gradient(180deg,
      #b9c6cc 0%, #c9d0cf 16%,
      #6f8791 26%, #6e8f52 34%,
      var(--water-blue) 44%, #9fb3bd 49%,
      #6fa83c 56%, var(--hill-green) 75%, #4f8a2a 100%);
  }
  .web-address {
    position: absolute;
    right: 30px;
    bottom: 30px;
    font-style: italic;
    font-weight: 700;
    font-size: 22px;
  }
  .map-sticker {
    position: absolute;
    right: 34px;
    top: 28px;
    width: 140px;
    height: 140px;
  }
  .map-sticker .sticker-text {
    position: absolute;
    inset: 0;
    display: flex;
    flex-direction: column;
    align-items: center;
    justify-content: center;
    transform: rotate(-10deg);
    line-height: 1.02;
    font-size: 26px;
  }
  .map-sticker .sticker-text strong { font-weight: 700; font-size: 29px; }
</style>
</head>
<body>
  <main class="canvas">
    <article class="cover">
      <div class="sky-photo" role="img" aria-label="Photograph of a blue sky with soft white clouds"></div>

      <header class="title-band">
        <h1 class="title-main">WHAREPUKE BAY</h1>
        <p class="title-sub"><span class="amp">&amp;</span>Its Hidden<br>&nbsp;&nbsp;&nbsp;&nbsp;&nbsp;&nbsp;&nbsp;Western Coves</p>
      </header>

      <div class="tagline-band">
        <p class="tagline">Old Stories, Diving, Tramping and places to see...</p>
      </div>

      <div class="landscape-photo" role="img" aria-label="Photograph of green rolling farmland with grazing cattle above a coastal harbour and distant hills"></div>

      <p class="web-address">www.wharepukebay.co.nz</p>

      <div class="map-sticker">
        <svg width="140" height="140" viewBox="0 0 140 140" aria-hidden="true">
          <circle cx="70" cy="70" r="68" fill="var(--sticker-blue)"/>
          <path d="M40 10 Q90 2 126 36 Q96 20 40 10 Z" fill="#7fa6f2"/>
        </svg>
        <div class="sticker-text">
          <span>Free</span>
          <strong>Handy</strong>
          <span>Map</span>
        </div>
      </div>
    </article>
  </main>
</body>
</html>
```